Flag Order

We were just looking to order some branding flags to put on our rental equipment for our business. We would like different examples of the colors, shapes, sizes, backgrounds etc. Was thinking of just doing the plains icon instead of the whole logo on there. but open to ideas. preferably not a white background as they could get dirty,

```html
<!DOCTYPE html>
<html lang="en">
<head>
<meta charset="utf-8">
<title>Keston Equipment Rentals – Feather Flags</title>
<link rel="stylesheet" href="https://fonts.googleapis.com/css2?family=Michroma&display=swap">
<style>
  :root {
    --backdrop: #1663a8;
    --flag-blue: #5b9fd8;
    --flag-white: #f4f4f4;
    --flag-black: #262626;
    --ink: #262626;
  }
  html, body {
    margin: 0;
    padding: 0;
    width: 1200px;
    height: 1200px;
    overflow: hidden;
    background: var(--backdrop);
  }
  .canvas {
    display: block;
    width: 1200px;
    height: 1200px;
  }
  .brand-name {
    font-family: "Michroma", "Arial Black", sans-serif;
    fill: var(--ink);
  }
  .brand-name--main { font-size: 56px; }
  .brand-name--sub { font-size: 14px; }
</style>
</head>
<body>
<svg class="canvas" viewBox="0 0 1200 1200" xmlns="http://www.w3.org/2000/svg">
  <defs>
    <clipPath id="feather-shape">
      <path d="M0 700 L0 300 C0 120 130 10 280 0 L272 700 Z"/>
    </clipPath>
    <g id="feather-flag">
      <g clip-path="url(#feather-shape)">
        <rect class="flag-field" x="0" y="0" width="290" height="700" fill="var(--flag-blue)"/>
        <rect class="flag-band" x="144" y="0" width="146" height="700" fill="var(--flag-white)"/>
        <polygon class="flag-base" points="0,444 290,585 290,700 0,700" fill="var(--flag-black)"/>
      </g>
      <rect class="brand-square" x="178" y="418" width="36" height="36" fill="var(--flag-blue)"/>
      <text class="brand-name brand-name--main" transform="translate(218 400) rotate(-90)" x="0" y="0" textLength="364" lengthAdjust="spacingAndGlyphs">KESTON</text>
      <text class="brand-name brand-name--sub" transform="translate(241 400) rotate(-90)" x="0" y="0" textLength="364" lengthAdjust="spacing">EQUIPMENT RENTALS</text>
    </g>
  </defs>

  <use class="flag flag--left" href="#feather-flag" x="256" y="250"/>
  <use class="flag flag--right" href="#feather-flag" x="664" y="250"/>
</svg>
</body>
</html>
```